Ravnaas-Lilleby Group AS

We need a design for our company including background pictures on our web (wix-template), redesign of logo and reports. Our company delivers personality test and services to clients when hiring staff or related to organizatonal developement.

Target Market(s)

Unisex, Age 30-50, managers in private corporations

Industry/Entity Type

Recruitment

Logo Text

Bygger laget sterkt (english translate: buids your team strong)

Number of Pages Required

1 page

Font styles to use
Sans Serif

Colors
add136
34a6d7
0255a3

Requirements
Must have
• The ideal designer will be the one to bring my narrative come to life. And it will have to include the testresults report and redesign (!) of my logo. Following the attached brief in ppt:
• - the testresult report
• - redesign logo
• - graphic elements in a maritime narrative
• - including the boat, the radar, 7 GULLs, the compass etc
Nice to have
• A strong narrative with a lot of elements.
• I really like the green color in the attached breif ;-)

```html
<!DOCTYPE html>
<html lang="en">
<head>
<meta charset="utf-8">
<title>Ravnaas-Lilleby Group AS</title>
<link href="https://fonts.googleapis.com/css2?family=Lora:wght@400;700&family=Montserrat:wght@400;500&family=Roboto:wght@400;700&display=swap" rel="stylesheet">
<style>
:root{
  --navy:#1f3a78;
  --ink:#1b1b1b;
  --muted:#555;
  --page:#e9e9eb;
  --white:#fff;
  --rule:#c9c9c9;
  --cell:#f0f0f0;
  --green:#6ec21e;
  --green-dark:#3f8f0d;
  --sky-top:#5a7390;
  --sky-bottom:#a9b2bb;
}
*{box-sizing:border-box;margin:0;padding:0}
html,body{width:1117px;height:1200px;overflow:hidden}
body{position:relative;background:var(--page);font-family:'Montserrat',sans-serif;color:var(--ink)}
.site-header{position:absolute;top:0;left:0;width:1117px;height:67px;background:var(--white);z-index:3}
.brand{position:absolute;left:124px;top:13px;width:120px}
.brand-name{font-family:'Lora',serif;font-weight:700;font-size:28px;line-height:28px;color:var(--navy);display:block;letter-spacing:1px}
.brand-tag{font-family:'Roboto',sans-serif;font-weight:700;font-size:8px;color:var(--navy);display:block;margin-top:3px;white-space:nowrap}
.main-nav{position:absolute;left:0;top:0;width:1117px;height:67px;font-family:'Lora',serif;font-size:12px;color:#333}
.main-nav span{position:absolute;top:26px;white-space:nowrap}
.main-nav .active{color:var(--navy)}
.phone{position:absolute;left:821px;top:22px;font-family:'Lora',serif;font-size:12px;color:#333;white-space:nowrap}
.phone b{font-size:17px;color:var(--navy);font-weight:400;margin-left:3px;vertical-align:-1px}
.lang{position:absolute;left:946px;top:23px;width:47px;height:19px;background:#eee;font-family:'Lora',serif;font-size:10px;line-height:19px;padding-left:5px;color:#333}
.lang i{display:inline-block;width:14px;height:9px;background:#2a3f8c;vertical-align:-1px;margin-right:3px}
.hero{position:absolute;top:67px;left:0;width:1117px;height:330px;background:linear-gradient(180deg,var(--sky-top) 0%,#7688a0 60%,var(--sky-bottom) 100%)}
.hero-title{position:absolute;left:124px;top:154px;font-family:'Lora',serif;font-weight:700;font-size:30px;line-height:29px;color:var(--white);text-shadow:0 2px 6px rgba(0,0,0,.45);z-index:2}
.card{position:absolute;left:302px;top:326px;width:513px;height:726px;background:var(--white);box-shadow:0 3px 4px rgba(0,0,0,.25)}
.compass{position:absolute;left:436px;top:243px;width:244px;height:244px;border-radius:50%;background:var(--white);z-index:2}
.compass-face{position:absolute;left:3px;top:3px;width:238px;height:238px;border-radius:50%;background:radial-gradient(circle,#e7edf5 0%,#c7d3e4 45%,#ffffff 60%,#dde5ef 80%,#0f3569 82%,#fff 84%,#fff 100%);border:3px solid #0f3569}
.meter{position:absolute}
.meter h3,.panel h3{font-weight:500;font-size:12px;color:var(--ink)}
.meter svg{display:block;margin-top:8px}
.panel{position:absolute;width:187px}
.panel-head{display:flex;align-items:center;height:26px}
.panel-head svg{margin-right:9px}
.results{margin-top:15px;width:187px;border:1px solid var(--rule);border-collapse:collapse;font-size:10px}
.results td{height:26px;border-bottom:1px solid var(--rule);padding-left:15px}
.results td+td{background:var(--cell);border-left:1px solid var(--rule);width:64px;padding-left:18px}
.results tr:last-child td{height:35px;border-bottom:none;vertical-align:top;padding-top:6px}
.testimonial{position:absolute;left:344px;top:894px;width:430px}
.avatar{position:absolute;left:0;top:0;width:94px;height:94px;border-radius:50%;background:radial-gradient(circle at 50% 40%,#c89d84 0%,#6b7c95 60%,#4b5f80 100%)}
.person{position:absolute;left:123px;top:0}
.person strong{display:block;font-weight:500;font-size:12px;letter-spacing:.3px}
.person span{display:block;font-weight:500;font-size:10px;margin-top:1px}
.divider{position:absolute;left:124px;top:37px;width:305px;height:2px;background:#ddd}
.quote{position:absolute;left:127px;top:58px;width:280px;font-family:'Roboto',sans-serif;font-size:10px;line-height:15px;color:#222}
.site-footer{position:absolute;left:0;top:1114px;width:1117px;height:86px;background:var(--white);text-align:center;font-family:'Roboto',sans-serif;font-size:12px;color:var(--muted);padding-top:34px}
</style>
</head>
<body>
<header class="site-header">
  <div class="brand"><span class="brand-name">RLG</span><span class="brand-tag">Rekruttering og utvikling</span></div>
  <nav class="main-nav">
    <span class="active" style="left:266px">Home</span>
    <span style="left:314px">Take the PAT test</span>
    <span style="left:430px">Jobs</span>
    <span style="left:477px">Product Presentation</span>
    <span style="left:606px">Company&nbsp; Presentation</span>
    <span style="left:748px">Contact Us</span>
  </nav>
  <div class="phone">Tel :<b>21 30 48 90</b></div>
  <div class="lang"><i></i>En &#9662;</div>
</header>

<section class="hero" role="img" aria-label="Business people looking through telescopes in a wide desert landscape"></section>
<h1 class="hero-title">Ravnaas-Lilleby<br>Group AS</h1>

<div class="compass"><div class="compass-face" role="img" aria-label="Navy compass rose with degree scale"></div></div>

<main class="card">
  <div class="meter" style="left:44px;top:207px">
    <h3>Energy</h3>
    <svg width="120" height="56" viewBox="0 0 120 56">
      <rect x="1" y="1" width="106" height="53" rx="5" fill="#d9d9d9" stroke="#bdbdbd"/>
      <rect x="107" y="17" width="11" height="21" rx="3" fill="#cfcfcf"/>
      <rect x="6" y="6" width="50" height="43" rx="3" fill="var(--green)"/>
      <rect x="10" y="12" width="42" height="28" rx="2" fill="var(--green-dark)" opacity=".55"/>
    </svg>
  </div>
  <div class="meter" style="left:289px;top:207px">
    <h3>Problem Solve</h3>
    <svg width="120" height="56" viewBox="0 0 120 56">
      <rect x="1" y="1" width="106" height="53" rx="5" fill="#d9d9d9" stroke="#bdbdbd"/>
      <rect x="107" y="17" width="11" height="21" rx="3" fill="#cfcfcf"/>
      <rect x="6" y="6" width="96" height="43" rx="3" fill="var(--green)"/>
      <rect x="10" y="12" width="88" height="28" rx="2" fill="var(--green-dark)" opacity=".55"/>
    </svg>
  </div>

  <section class="panel" style="left:46px;top:330px">
    <div class="panel-head">
      <svg width="28" height="20" viewBox="0 0 28 20"><path d="M2 7h5l11-6v18L7 13H5l2 6H4l-2-6z" fill="var(--navy)"/><path d="M21 6q3 4 0 8M24 3q5 7 0 14" stroke="var(--navy)" stroke-width="1.6" fill="none"/></svg>
      <h3>Listen</h3>
    </div>
    <table class="results">
      <tr><td>Lorem Ipsum</td><td>15.38</td></tr>
      <tr><td>It is a long est</td><td>25.5</td></tr>
      <tr><td>Oposed to using</td><td>212.25</td></tr>
      <tr><td>Model tex</td><td>21.20</td></tr>
      <tr><td>Simply rando</td><td>15.36</td></tr>
    </table>
  </section>

  <section class="panel" style="left:289px;top:330px">
    <div class="panel-head">
      <svg width="24" height="24" viewBox="0 0 24 24"><circle cx="12" cy="12" r="11" fill="none" stroke="var(--navy)" stroke-width="1.4"/><circle cx="12" cy="12" r="7" fill="none" stroke="var(--navy)" stroke-width="1.2"/><circle cx="12" cy="12" r="3" fill="var(--navy)"/><path d="M12 12l6-7" stroke="var(--navy)" stroke-width="1.6"/></svg>
      <h3>Sending</h3>
    </div>
    <table class="results">
      <tr><td>Lorem Ipsum</td><td>15.38</td></tr>
      <tr><td>It is a long est</td><td>25.5</td></tr>
      <tr><td>Oposed to using</td><td>212.25</td></tr>
      <tr><td>Model tex</td><td>21.20</td></tr>
      <tr><td>Simply rando</td><td>15.36</td></tr>
    </table>
  </section>
</main>

<section class="testimonial">
  <div class="avatar" role="img" aria-label="Portrait photo of the reviewer"></div>
  <div class="person"><strong>DANIEL MORTENSEN</strong><span>NORVIK SYSTEMS, UK</span></div>
  <div class="divider"></div>
  <p class="quote">There are many variations of passages of Lorem Ipsum available, but the majority have suffered alteration in some form, by injected humour, or randomised words which don't look even slightly believabl</p>
</section>

<footer class="site-footer">Copyrights @ 2017 All Rights Reserved</footer>
</body>
</html>
```